Wordpress Theme for Medical Clinics

** Please view updated Sitemap2.pdf doc to clarify some confusion ***

This is a multiuser WordPress subscription site for medical clinics. Please see attachment for sitemap. Please do not include extra content like social media icons, search bars, or images. If you have questions, please ask for clarification.
The site contains the following pages and sub-pages:

1. Home
2. Our Clinic
2a. Our Clinic > Mission
2b. Our Clinic > Services
2c. Our Clinic > Clinic Policies
2d. Our Clinic > Schedules
3. Our Staff
3a. Our Staff > [Staff member page]
4. Resources
4a. Resources > Patient Health (index)
4b. Resources > Patient Health (index) > [post]
4c. Resources > Links
4d. Resources > Forms
5. Alerts
5a. Alerts > [Alert Page]
6. Contact Us

Includes the Following Pages, Subpages, and Content
1. Home
a. About Us
b. Our Staff
c. Bulletins
d. Accepting New Patients (shown as an alert widget)
e. Links
i. Physician Toolbox
ii. Book an Appointment
f. Clinic Policies
i. Show first 3 policies (e.g. Late Arrivals, Missed Appointments, Fees)
ii. Link to Clinic Policies page
g. Primary widget (displayed on all pages)
i. Hours of operation
ii. Contact Info
1. Tel
2. Fax
3. Email
4. Address
5. Get directions (link to Google Maps)
2. Our Clinic
a. Main Page
i. Harbor Clinic
ii. Overview
iii. Languages Spoken
iv. Secondary Navigation
1. Mission
2. Services
3. Clinic Policies
4. Schedules (see attachment)
b. Our Clinic > Mission
c. Our Clinic > Services
i. For each service include service TITLE and DESCRIPTION
d. Our Clinic > Clinic Policies
i. For each policy include policy TITLE and DESCRIPTION
ii. Include the following policies in mockup
1. Late arrivals
2. Missed appointments
3. Fees for missed appointments
4. Referrals and follow-ups
5. Services not covered by RDA
6. Information for LTF patients
7. Medical Legal Reports
e. Our Clinic > Schedules
3. Our Staff
a. Main Page
i. Display a list of staff members. Include NAME and DESIGNATION
b. Our Staff > [Staff Name]
i. Include NAME, PICTURE, DESIGNATION, and BIO
4. Resources
a. Resources > Patient Health
i. Main Page
1. Posts (ordered by date)
a. Title
b. Summary
2. Side Navigation
a. Post Categories
ii. Patient Health > [post title]
1. Title
2. Post Category
3. Date
4. Author
5. Summary
6. Body
b. Resources > Links
1. Secondary Navigation - Categories
a. Sample Categories:
i. Local Services
ii. RDA and Drug Coverage
iii. Mental Health Resources
2. Category page
a. Include the following links in the 'Local Services' category
i. Hypertension clinics
ii. Home Care services
iii. Vaccine Clinics
c. Resources > Forms
i. Display a table with form TITLE and CATEGORY
ii. Side Navigation
1. Form Categories
a. Use the following sample Categories
i. Referrals
ii. Insurance
iii. Intake
iv. Discharge
v. Waivers
5. Alerts
a. Main page
i. List of all Alert posts
1. Include post TITLE as a link to the post
ii. Side Navigation
1. Alerts Archive
a. shown as Month + Number of posts
iii. Alerts > [Alert page]
1. Include TITLE, DATE, AUTHOR, BODY
6. Contact Us
a. Map
b. Hours of operation
c. Address
d. Phone number
e. Fax number
e. Fax number
f. Map
g. Email

Design notes:
- fixed width
- responsive (need designs for mobile, tablet, and desktop)
- simple, dark font, white background
- use Font Awesome icons where needed
- user adds own logo

Target Market(s)

Medical Clinics

Industry/Entity Type

Medical

Number of Pages Required

5+ page

Font styles to use
Serif
Sans Serif

Requirements
Must have
• Please keep designs very simple.
• Examples:
• https://www.quolbin.com/install
• http://www.ventrohax.com/company/about-us
• http://brindlequota.org/
• http://www.trosk.com/
Should not have
• Minimal or no use of shadows and gradients

```html
<!DOCTYPE html>
<html lang="en">
<head>
<meta charset="utf-8">
<title>Harbor Clinic – Home</title>
<link href="https://fonts.googleapis.com/css2?family=Kaushan+Script&family=Roboto:wght@300;400;500;700&display=swap" rel="stylesheet">
<style>
:root{
  --blue:#4aaef0;
  --blue-mid:#1b86d8;
  --blue-dark:#2d55a3;
  --blue-deep:#0c5a9e;
  --footer:#0a7ad1;
  --ink:#2b2b2b;
  --text:#555;
  --muted:#888;
  --line:#e3e3e3;
  --hero:#dcebf7;
  --charcoal:#3c3c3c;
}
*{margin:0;padding:0;box-sizing:border-box}
html,body{width:700px;height:1200px;overflow:hidden}
body{position:relative;background:#fff;font-family:"Roboto",Arial,sans-serif;color:var(--text)}
.abs{position:absolute}
.ph{position:absolute}

/* top bar */
.topbar{top:0;left:0;width:700px;height:22px;border-bottom:1px solid var(--line);font-size:6.5px;color:var(--muted)}
.topbar span{position:absolute;top:7px;display:flex;align-items:center;gap:5px}
.topbar .sep{position:absolute;top:0;width:1px;height:21px;background:var(--line)}
.topbar svg{width:8px;height:8px}

/* header */
.logo{top:33px;left:73px;font-size:17px;font-weight:700;color:var(--blue-mid);letter-spacing:.2px}
.nav{top:22px;left:303px;display:flex;height:40px;font-size:6.5px;font-weight:500;color:var(--muted)}
.nav a{display:flex;align-items:center;padding:0 10px;color:inherit;text-decoration:none}
.nav a.active{background:var(--blue);color:#fff;width:38px;justify-content:center;padding:0}
.nav a.contact{color:var(--blue-mid)}

/* hero */
.hero{top:62px;left:0;width:700px;height:340px;background:linear-gradient(90deg,#d6e8f6,#e6f1fa 60%,#d9e9f6)}
.hero-title{top:86px;left:73px;font-family:"Kaushan Script",cursive;font-size:42px;color:#1e1e1e}
.hero-sub{top:144px;left:71px;font-size:26px;font-weight:300;color:#1f5d8e}
.hero-rule{top:180px;left:73px;width:272px;height:1px;background:#9bb7cc}
.hero-copy{top:186px;left:73px;width:280px;font-size:6.8px;line-height:10px;color:#333}
.btn-hero{top:213px;left:73px;width:107px;height:27px;background:var(--blue);color:#fff;font-size:8px;display:flex;align-items:center;justify-content:center}
.dots{top:259px;left:73px;display:flex;gap:3px}
.dots i{width:5px;height:5px;border-radius:50%;border:1px solid #555;display:block}
.dots i:first-child{background:#555}
.doctor{top:78px;left:425px;width:215px;height:206px;background:linear-gradient(180deg,#e9eef2,#c9d8e4);border-radius:2px}

/* hero panels */
.panel{color:#fff}
.panel h3{font-size:10px;font-weight:500;letter-spacing:.3px}
.new-patients{top:284px;left:65px;width:190px;height:118px;background:var(--blue);padding:13px 13px}
.new-patients .row{margin-top:10px;border-bottom:1px solid rgba(255,255,255,.6);padding-bottom:5px;font-size:6.5px;display:flex;justify-content:space-between}
.new-patients p{margin-top:8px;font-size:5.6px;line-height:8px}
.hours{top:254px;left:255px;width:190px;height:148px;background:var(--blue-mid)}
.hours h3{position:absolute;top:15px;left:14px}
.hours-table{position:absolute;top:36px;left:18px;width:161px;table-layout:fixed;border-collapse:collapse;font-size:5.5px;text-align:center}
.hours-table td{width:23px;padding:0;border:1px solid rgba(255,255,255,.35)}
.hours-table tr.days td{height:20px;background:#fff;color:#333;border-color:#cfe3f3}
.hours-table tr.open td{height:24px;background:var(--blue-deep);line-height:7px}
.hours-table tr.close td{height:24px;background:var(--blue);line-height:7px}
.hours-table b{font-size:7.5px;font-weight:500;display:block}
.vlab{position:absolute;left:7px;font-size:5px;transform:rotate(-90deg);transform-origin:left top}
.hours-foot{position:absolute;left:0;bottom:0;width:190px;height:29px;display:flex;background:var(--charcoal);font-size:6.5px;font-weight:500}
.hours-foot span{flex:1;display:flex;align-items:center;justify-content:center}
.hours-foot span+span{border-left:1px solid #555}
.services{top:284px;left:445px;width:190px;height:118px;background:var(--blue-dark);padding:13px 13px}
.services ul{list-style:none;margin-top:9px}
.services li{font-size:6.5px;height:18px;display:flex;align-items:center;justify-content:space-between;border-bottom:1px solid rgba(255,255,255,.35)}

/* section headings */
.sec-title{font-size:10px;font-weight:400;color:#333;letter-spacing:.3px}
.sec-title::after{content:"";display:block;width:26px;height:2px;background:var(--blue);margin-top:5px}
.btn{position:absolute;height:15px;font-size:5.8px;color:#fff;display:flex;align-items:center;justify-content:center}
.btn.light{background:var(--blue)}
.btn.dark{background:#0f70bf}

/* our clinic */
.clinic-photo{top:451px;left:73px;width:175px;height:89px;background:linear-gradient(90deg,#cfd9e2,#eef1f3 50%,#6a9ccc)}
.clinic-head{top:450px;left:263px;font-size:11px;color:var(--blue);font-weight:400}
.clinic-head::after{content:"";display:block;width:26px;height:2px;background:var(--blue);margin-top:5px}
.clinic-copy{top:476px;left:263px;width:173px;font-size:5.8px;line-height:8px;color:var(--text)}
.divider{height:1px;background:var(--line)}

/* alerts */
.tag{position:absolute;height:14px;display:flex;font-size:5.6px;color:#fff}
.tag span{display:flex;align-items:center;padding:0 7px;background:var(--blue)}
.tag b{display:flex;align-items:center;padding:0 5px;background:var(--blue-mid);font-weight:500}
.tag span::after{content:"";position:absolute;left:18px;top:14px;border:3px solid transparent;border-top-color:var(--blue)}
.alert-photo{width:175px;height:98px}
.caption{width:175px;text-align:center;font-size:5.8px;color:#333;padding-bottom:8px;border-bottom:1px solid var(--line)}

/* right column */
.policy-bar{top:451px;left:453px;width:175px;height:18px;background:var(--blue);color:#fff;font-size:6.5px;padding-left:7px;display:flex;align-items:center}
.policy-photo{top:477px;left:453px;width:68px;height:48px;background:linear-gradient(135deg,#e4d9d1,#a8b9c6)}
.policy-copy{top:479px;left:530px;width:96px;font-size:5.6px;line-height:7.5px}
.accordion{top:529px;left:453px;width:175px;list-style:none;font-size:6.5px;color:#666}
.accordion li{height:17px;display:flex;align-items:center;justify-content:space-between;padding-left:8px;border-bottom:1px solid var(--line);border-top:1px solid transparent}
.accordion li:first-child{border-top-color:var(--line)}
.accordion em{font-style:normal;font-size:10px;color:#666;padding-right:6px}
.contact-copy{top:664px;left:453px;width:175px;font-size:5.8px;line-height:8px}
.contact-list{top:694px;left:453px;width:175px;list-style:none;font-size:5.8px;color:#444;border-top:1px dotted #ccc}
.contact-list li{height:19px;display:flex;align-items:center;border-bottom:1px dotted #ccc}
.contact-list svg{width:7px;height:7px;margin-right:8px}
.contact-list .val{margin-left:auto;color:var(--blue-mid)}

/* staff */
.staff-arrow{position:absolute;top:826px;width:18px;height:17px;border:1px solid #bbb;display:flex;align-items:center;justify-content:center}
.staff-card{position:absolute;top:857px;width:128px;text-align:center}
.staff-photo{width:128px;height:124px}
.staff-name{margin-top:7px;font-size:8px;color:var(--blue)}
.staff-role{margin-top:3px;font-size:6px;color:#333}
.staff-bar{margin-top:8px;height:3px;background:var(--blue)}
.overlay{position:absolute;top:0;left:0;width:128px;height:124px;background:rgba(74,174,240,.85)}
.sq{position:absolute;top:82px;width:20px;height:20px;border:1px solid rgba(255,255,255,.8)}

/* footer */
.footer{top:1043px;left:0;width:700px;height:126px;background:var(--footer);color:#fff}
.fcol{position:absolute;top:20px}
.fcol h4{font-size:8.5px;font-weight:500;margin-bottom:9px}
.fcol ul{list-style:none;font-size:6.5px}
.fcol li{height:16px;display:flex;align-items:center;border-bottom:1px solid rgba(255,255,255,.35)}
.fcol li svg{width:7px;height:7px;margin-right:7px}
.fsep{position:absolute;top:22px;width:1px;height:84px;background:rgba(255,255,255,.35)}
.hours-grid{display:grid;grid-template-columns:75px 75px;column-gap:0;font-size:6.3px}
.hours-grid div{height:16px;display:flex;align-items:center;justify-content:space-between;padding-right:8px}
.hours-grid b{font-weight:700;font-size:6.8px}
.copyright{top:1180px;left:0;width:700px;text-align:center;font-size:6.5px;color:#444}
.copyright b{color:var(--blue-mid);font-weight:500}
</style>
</head>
<body>

<!-- top utility bar -->
<div class="abs topbar">
  <span style="left:73px"><svg viewBox="0 0 10 10"><path d="M2 1v4a3 3 0 0 0 6 0V1" fill="none" stroke="#999"/></svg>Physician Toolbox</span>
  <div class="sep" style="left:152px"></div>
  <span style="left:160px"><svg viewBox="0 0 10 10"><circle cx="5" cy="5" r="4" fill="none" stroke="#999"/><path d="M5 2.5V5h2" fill="none" stroke="#999"/></svg>Book an Appointment</span>
  <div class="sep" style="left:245px"></div>
  <div class="sep" style="left:405px"></div>
  <span style="left:418px"><svg viewBox="0 0 10 10"><path d="M1 8l8-6-3 7-1.5-2.5z" fill="none" stroke="#999"/></svg>Send Mail: info@harborclinic.com</span>
  <div class="sep" style="left:531px"></div>
  <span style="left:542px"><svg viewBox="0 0 10 10"><path d="M2 1h2l1 2-1.2 1A5 5 0 0 0 6 6.2L7 5l2 1v2c-4 0-7-3-7-7z" fill="none" stroke="#999"/></svg>Call Us: 0800 - 555 - 90</span>
</div>

<!-- header -->
<div class="abs logo">Harbor Clinic</div>
<nav class="abs nav">
  <a class="active">HOME</a>
  <a style="margin-left:10px">OUR CLINIC</a>
  <a>STAFF</a>
  <a>RESOURCES</a>
  <a>ALERTS</a>
  <a class="contact">CONTACT US</a>
</nav>

<!-- hero -->
<div class="ph hero" role="img" aria-label="Soft blurred photo of a clinic interior"></div>
<div class="ph doctor" role="img" aria-label="Photo of a smiling doctor holding a clipboard"></div>
<div class="abs hero-title">Quality Care !</div>
<div class="abs hero-sub">Provided For everyone...</div>
<div class="abs hero-rule"></div>
<p class="abs hero-copy">Highly skilled and Experienced medical staff comfortable and cosy patient room, state -of-theart dianostic equipment.</p>
<div class="abs btn-hero">Book an Appointment</div>
<div class="abs dots"><i></i><i></i><i></i></div>

<!-- new patients -->
<div class="abs panel new-patients">
  <h3>NEW PATIENTS</h3>
  <svg class="abs" style="top:12px;right:13px" width="14" height="14" viewBox="0 0 14 14"><circle cx="6" cy="2" r="1.5" fill="#fff"/><path d="M6 4v4h4l2 4M4 7a4 4 0 1 0 5 5" fill="none" stroke="#fff" stroke-width="1.3"/></svg>
  <div class="row"><span>Accepting New Patients</span><svg width="9" height="7" viewBox="0 0 9 7"><path d="M0 3.5h8M5 .5l3 3-3 3" fill="none" stroke="#fff"/></svg></div>
  <p>Lorem ipsum dolor sit amet, consectetuer adipiscing elit,sss sed diam nonummy nibh euismod tincidunt ut laoreet dolore magna aliquam erat volutpat. sxsx Ut wisi enim ad minim veniam, xcqdwdqe wdadagty yt quis nostrud exerci tationsi. magna aliquam erat volutpat. sxsx Ut wisi enim ad minim</p>
</div>

<!-- opening hours -->
<div class="abs panel hours">
  <h3>OPENING HOURS</h3>
  <svg class="abs" style="top:12px;right:10px" width="14" height="14" viewBox="0 0 14 14"><rect x="1" y="2" width="12" height="11" rx="1" fill="none" stroke="#fff"/><path d="M1 5h12M4 1v2M10 1v2M3 7h8M3 9h8M3 11h8" stroke="#fff" stroke-width=".8"/></svg>
  <span class="vlab" style="top:78px">OPEN</span>
  <span class="vlab" style="top:104px">CLOSE</span>
  <table class="hours-table">
    <tr class="days"><td>Mon</td><td>Tue</td><td>Wed</td><td>Thu</td><td>Fri</td><td>Sat</td><td>Sun</td></tr>
    <tr class="open"><td><b>8</b>AM</td><td><b>8</b>AM</td><td><b>8</b>AM</td><td><b>8</b>AM</td><td><b>8</b>AM</td><td><b>9</b>AM</td><td><b>9</b>AM</td></tr>
    <tr class="close"><td><b>6</b>PM</td><td><b>6</b>PM</td><td><b>6</b>PM</td><td><b>6</b>PM</td><td><b>6</b>PM</td><td><b>4</b>PM</td><td><b>4</b>PM</td></tr>
  </table>
  <div class="hours-foot"><span>APPOINTMENT</span><span>HOLIDAY HOURS!</span></div>
</div>

<!-- services -->
<div class="abs panel services">
  <h3>SERVICES</h3>
  <svg class="abs" style="top:12px;right:13px" width="14" height="14" viewBox="0 0 14 14"><path d="M6 8l2-2M5 6l-2 2a2 2 0 0 0 3 3l2-2M9 8l2-2a2 2 0 0 0-3-3L6 5" fill="none" stroke="#fff" stroke-width="1.3"/></svg>
  <ul>
    <li>LTF Clinics<svg width="9" height="7" viewBox="0 0 9 7"><path d="M0 3.5h8M5 .5l3 3-3 3" fill="none" stroke="#fff"/></svg></li>
    <li>LTF Clinics<svg width="9" height="7" viewBox="0 0 9 7"><path d="M0 3.5h8M5 .5l3 3-3 3" fill="none" stroke="#fff"/></svg></li>
    <li>LTF Clinics<svg width="9" height="7" viewBox="0 0 9 7"><path d="M0 3.5h8M5 .5l3 3-3 3" fill="none" stroke="#fff"/></svg></li>
    <li>LTF Clinics<svg width="9" height="7" viewBox="0 0 9 7"><path d="M0 3.5h8M5 .5l3 3-3 3" fill="none" stroke="#fff"/></svg></li>
  </ul>
</div>

<!-- our clinic -->
<h2 class="abs sec-title" style="top:423px;left:73px">OUR CLINIC !</h2>
<div class="ph clinic-photo" role="img" aria-label="Photo of a doctor working in a clinic laboratory"></div>
<h3 class="abs clinic-head">LOREM IPSUM DOLOR SIT AMET !</h3>
<p class="abs clinic-copy">Lorem ipsum dolor sit amet, consectetuer adipiscing elit, sed diam nonummy nibbhy euismod tincidunt ut laoreet dolore magna sadx aliquam erat volutpat. Ut wisi bys enim ads minim veniam, uahasex by ags sea commodo conat..</p>
<div class="btn light" style="top:517px;left:263px;width:40px">More</div>
<div class="btn dark" style="top:517px;left:309px;width:41px">About</div>
<div class="abs divider" style="top:555px;left:73px;width:365px"></div>

<!-- latest alerts -->
<h2 class="abs sec-title" style="top:570px;left:73px">LATEST ALERTS</h2>
<div class="tag" style="top:601px;left:73px"><span>JUNE 2015</span><b>12</b></div>
<div class="tag" style="top:601px;left:263px"><span>JUNE 2015</span><b>12</b></div>
<div class="ph alert-photo" style="top:628px;left:73px;background:linear-gradient(90deg,#e8ecef,#c8d5df 50%,#efe6da)" role="img" aria-label="Photo of a doctor talking with a patient"></div>
<div class="ph alert-photo" style="top:628px;left:263px;background:linear-gradient(90deg,#eef0f2,#bcd0de 45%,#e4e6e8)" role="img" aria-label="Photo of a doctor comforting an older patient"></div>
<div class="abs caption" style="top:735px;left:73px">LOREM IPSUM DOLOR SIT AMET !</div>
<div class="abs caption" style="top:735px;left:263px">LOREM IPSUM DOLOR SIT AMET !</div>
<div class="btn light" style="top:764px;left:73px;width:42px">View More</div>

<!-- clinic policies -->
<h2 class="abs sec-title" style="top:423px;left:453px">CLINIC POLICIES !</h2>
<div class="abs policy-bar">Late Arrivals !</div>
<div class="ph policy-photo" role="img" aria-label="Photo of a nurse caring for a patient"></div>
<p class="abs policy-copy">Lorem ipsum dolor sit ame ctetuer adipiscingt, sed diam nonummys nibh euismod tinc ut wisi..</p>
<div class="btn light" style="top:506px;left:530px;width:33px">More</div>
<ul class="abs accordion">
  <li>Missed Appointments<em>+</em></li>
  <li>Fees For Missed Appointments<em>+</em></li>
  <li>Missed Appointments<em>+</em></li>
</ul>
<div class="btn light" style="top:592px;left:453px;width:42px">View More</div>

<!-- contact info -->
<h2 class="abs sec-title" style="top:637px;left:453px">CONTACT INFO !</h2>
<p class="abs contact-copy">Lorem ipsum dolor sit amet, consectetuer adipiscingt, sed diam aliquam erat volutpat. Ut wisi...</p>
<ul class="abs contact-list">
  <li><svg viewBox="0 0 10 10"><path d="M2 1h2l1 2-1.2 1A5 5 0 0 0 6 6.2L7 5l2 1v2c-4 0-7-3-7-7z" fill="var(--blue)"/></svg>Phone<span class="val">804-555-0199</span></li>
  <li><svg viewBox="0 0 10 10"><path d="M1 8l8-6-3 7-1.5-2.5z" fill="none" stroke="var(--blue)"/></svg>Email<span class="val">desk@harborclinic.com</span></li>
  <li><svg viewBox="0 0 10 10"><path d="M5 9.5S1.5 6 1.5 4a3.5 3.5 0 0 1 7 0c0 2-3.5 5.5-3.5 5.5z" fill="var(--blue)"/><circle cx="5" cy="4" r="1.2" fill="#fff"/></svg>Address<span class="val">48 Elm Row , Ashford</span></li>
</ul>
<div class="btn light" style="top:764px;left:453px;width:42px">View More</div>

<!-- our staff -->
<div class="abs divider" style="top:801px;left:0;width:700px"></div>
<h2 class="abs sec-title" style="top:825px;left:73px">OUR STAFF !</h2>
<div class="staff-arrow" style="left:588px"><svg width="5" height="7" viewBox="0 0 5 7"><path d="M4 .5l-3 3 3 3" fill="none" stroke="#888"/></svg></div>
<div class="staff-arrow" style="left:610px"><svg width="5" height="7" viewBox="0 0 5 7"><path d="M1 .5l3 3-3 3" fill="none" stroke="#888"/></svg></div>

<div class="staff-card" style="left:73px">
  <div class="ph staff-photo" style="position:relative;background:linear-gradient(135deg,#d9e4ec,#8fb3cf)" role="img" aria-label="Photo of a group of medical staff"></div>
  <div class="staff-name">Dr. Alan Marsh.&nbsp; MD</div><div class="staff-role">Surgon</div><div class="staff-bar"></div>
</div>
<div class="staff-card" style="left:215px">
  <div class="ph staff-photo" style="position:relative;background:linear-gradient(135deg,#cfe1ee,#8db8da)" role="img" aria-label="Photo of a doctor with profile link overlay">
    <div class="overlay"></div>
    <div class="sq" style="left:41px"></div>
    <div class="sq" style="left:66px"></div>
  </div>
  <div class="staff-name">Dr. Alan Marsh.&nbsp; MD</div><div class="staff-role">Surgon</div><div class="staff-bar"></div>
</div>
<div class="staff-card" style="left:358px">
  <div class="ph staff-photo" style="position:relative;background:linear-gradient(135deg,#eef1f3,#c5d4de)" role="img" aria-label="Photo of a doctor reading a tablet"></div>
  <div class="staff-name">Dr. Alan Marsh.&nbsp; MD</div><div class="staff-role">Surgon</div><div class="staff-bar"></div>
</div>
<div class="staff-card" style="left:500px">
  <div class="ph staff-photo" style="position:relative;background:linear-gradient(135deg,#e3edf1,#7fc6c3)" role="img" aria-label="Photo of a surgeon in scrubs holding a clipboard"></div>
  <div class="staff-name">Dr. Alan Marsh.&nbsp; MD</div><div class="staff-role">Surgon</div><div class="staff-bar"></div>
</div>

<!-- footer -->
<footer class="abs footer">
  <div class="fcol" style="left:85px;width:75px">
    <h4>OUR CLINIC</h4>
    <ul><li>Mission</li><li>Services</li><li>Schedules</li><li>Policies</li></ul>
  </div>
  <div class="fsep" style="left:183px"></div>
  <div class="fcol" style="left:207px;width:77px">
    <h4>RESOURCES</h4>
    <ul><li>Our clinic</li><li>Mission</li><li>Services</li></ul>
  </div>
  <div class="fsep" style="left:306px"></div>
  <div class="fcol" style="left:330px;width:92px">
    <h4>CONTACT US</h4>
    <ul>
      <li><svg viewBox="0 0 10 10"><path d="M2 1h2l1 2-1.2 1A5 5 0 0 0 6 6.2L7 5l2 1v2c-4 0-7-3-7-7z" fill="#fff"/></svg>123-555-0147</li>
      <li><svg viewBox="0 0 10 10"><rect x="1" y="2" width="8" height="6" fill="#fff"/><path d="M1 2l4 3 4-3" fill="none" stroke="var(--footer)"/></svg>contact@harborclinic.com</li>
      <li><svg viewBox="0 0 10 10"><path d="M5 9.5S1.5 6 1.5 4a3.5 3.5 0 0 1 7 0c0 2-3.5 5.5-3.5 5.5z" fill="#fff"/></svg>48 Elm Row , Ashford</li>
    </ul>
  </div>
  <div class="fsep" style="left:462px"></div>
  <div class="fcol" style="left:478px;width:150px">
    <h4>HOURS OF OPERATION</h4>
    <div class="hours-grid">
      <div>Mon<b>8 AM - 6 PM</b></div><div>Fri<b>8 AM - 6 PM</b></div>
      <div>Tue<b>8 AM - 6 PM</b></div><div>Sat<b>9 AM - 4 PM</b></div>
      <div>Wed<b>8 AM - 6 PM</b></div><div>Sun<b>9 AM - 4 PM</b></div>
      <div>Thu<b>8 AM - 6 PM</b></div><div style="justify-content:flex-end"><b style="font-size:5.8px">Holiday Hours !</b></div>
    </div>
  </div>
</footer>
<p class="abs copyright">© 2015 Copyright.<b>HarborClinic</b>.com</p>

</body>
</html>
```